WordPress webdesign with coding for our company BRISK The Answer

BRISK The Answer is a payrolling company such as Montaval Wages (one of our competitor https://www.montaval-wages.ch/fr/). We need to set up our website in both languages (Fr and Eng). Our logo is enclosed.
we would like something simple explaining what is payrolling in Graph and wording, who we are and a contact page. you can also take some example if needed from our mother company BRISK The Horizon (www.briskthehorizon.ch) or our sister company (www.briskyourstride.ch). we would like to keep the color panel of our logo (ref. Black = PANTONE P Process Black C
Pink = PANTONE P Process Magenta C
Grey = PANTONE 430 C) as the driver of the website.

```html
<!DOCTYPE html>
<html lang="en">
<head>
<meta charset="utf-8">
<title>BRISK The Answer – Payrolling Solutions</title>
<link rel="stylesheet" href="https://fonts.googleapis.com/css2?family=Outfit:wght@500;600;700&family=Roboto:wght@400;500;700&display=swap">
<style>
:root{
  --pink:#e6007e;
  --pink-dark:#b8006a;
  --pink-soft:#fde8f2;
  --ink:#231f20;
  --grey:#a7a8aa;
  --field:#efefef;
  --text:#555;
  --white:#fff;
}
*{box-sizing:border-box;margin:0;padding:0}
html,body{width:1200px;height:4651px;overflow:hidden}
body{position:relative;background:var(--white);font-family:'Roboto',sans-serif;color:var(--ink)}
.abs{position:absolute}
.heading{font-family:'Outfit',sans-serif;font-weight:600;color:var(--ink);text-align:center;width:100%;left:0}
.kicker{font-family:'Outfit',sans-serif;font-weight:500;color:var(--pink);text-align:center;width:100%;left:0;font-size:22px}
.btn{position:absolute;background:var(--pink);color:#fff;border-radius:30px;display:flex;align-items:center;justify-content:center;font-weight:700;font-size:14px}

/* hero */
.hero-photo{left:0;top:0;width:1200px;height:760px;background:linear-gradient(110deg,#1b1d27 0%,#2b2f3c 45%,#5a5f6b 75%,#3a3d46 100%)}
.hero-shapes{left:0;top:0}
.nav{left:112px;top:50px;width:976px;height:76px;background:#fff;border-radius:40px;box-shadow:0 4px 18px rgba(0,0,0,.15)}
.brand{position:absolute;font-family:'Outfit',sans-serif;font-weight:600;color:var(--ink);letter-spacing:1px}
.nav .brand{left:25px;top:10px;font-size:38px;line-height:40px}
.nav .brand small{display:block;font-size:9px;letter-spacing:6px;line-height:10px;font-weight:500}
.nav-link{position:absolute;top:30px;font-size:13px;font-weight:500;color:var(--ink)}
.lang{position:absolute;left:906px;top:13px;width:50px;height:50px;border:2px solid var(--pink);border-radius:50%;font-size:10px;font-weight:700;display:flex;flex-direction:column;align-items:center;justify-content:center;gap:2px}
.hero-title{left:112px;top:196px;font-family:'Outfit',sans-serif;font-weight:700;font-size:50px;line-height:59px;color:#fff}
.hero-text{left:112px;top:384px;width:395px;font-size:15.5px;line-height:29px;color:#fff}

/* about */
.about-ring{left:112px;top:876px;width:536px;height:536px;border-radius:50%;background:var(--ink)}
.about-ring::after{content:"";position:absolute;left:64px;top:64px;width:408px;height:408px;border-radius:50%;background:#fff}
.about-photo{left:172px;top:939px;width:414px;height:414px;border-radius:50%;border:9px solid #fff;box-shadow:0 6px 24px rgba(0,0,0,.25);background:radial-gradient(circle at 45% 40%,#f1e5d8 0%,#d9c9b6 45%,#8b8f94 100%)}
.about-text{left:645px;width:430px;text-align:center;font-size:14.5px;line-height:29px;color:var(--text)}

/* steps */
.step{top:1716px;width:227px;height:242px;background:var(--pink-soft);border-radius:18px;text-align:center}
.step .ico{position:absolute;left:78px;top:41px;width:70px;height:70px;border-radius:50%;background:var(--pink);display:flex;align-items:center;justify-content:center}
.step h4{position:absolute;top:127px;width:100%;font-size:15px;font-weight:700}
.step p{position:absolute;top:156px;left:20px;right:20px;font-size:13.5px;line-height:25px;color:var(--text)}

/* payrolling */
.pay-card{left:168px;top:2257px;width:864px;height:543px;background:#fff;border-radius:40px;box-shadow:0 14px 30px rgba(0,0,0,.18)}
.dot{position:absolute;width:86px;height:86px;border-radius:50%;display:flex;align-items:center;justify-content:center;box-shadow:0 6px 14px rgba(0,0,0,.25)}
.flow-label{position:absolute;font-size:13px;font-weight:500;text-align:center;width:200px}
.list-item{position:absolute;font-size:14px;line-height:29px;color:var(--ink)}
.list-item b{color:var(--pink);font-weight:500}

/* services */
.svc{top:3024px;width:318px;height:450px;border:1.5px solid var(--pink);border-radius:24px;overflow:hidden;background:#fff;box-shadow:0 8px 18px rgba(0,0,0,.12);text-align:center}
.svc .pic{height:305px}
.svc h4{margin-top:24px;font-size:18px;font-weight:500;line-height:26px}
.svc p{margin:4px 20px 0;font-size:14px;line-height:25px;color:var(--text)}

/* contact */
.field{position:absolute;background:var(--field);border-radius:25px;display:flex;align-items:center;gap:12px;padding-left:34px;font-size:12px;color:#444}

/* footer */
.foot-h{position:absolute;font-family:'Outfit',sans-serif;font-size:22px;font-weight:500;color:var(--pink)}
.foot-i{position:absolute;font-size:14px;color:#fff;display:flex;align-items:center;gap:16px}
.social{position:absolute;top:4343px;width:38px;height:38px;border-radius:50%;background:var(--pink);border:2px solid #fff}
</style>
</head>
<body>

<!-- HERO -->
<div class="abs hero-photo" role="img" aria-label="Photo of a business meeting in a glass-walled office"></div>
<svg class="abs hero-shapes" width="1200" height="780" viewBox="0 0 1200 780">
  <polygon points="0,550 352,722 1200,505 1200,780 0,780" fill="#fff"/>
  <polygon points="63,596 352,765 1045,578 352,718" fill="var(--pink)"/>
</svg>

<nav class="abs nav">
  <div class="brand">BRISK<small>THE ANSWER</small></div>
  <span class="nav-link" style="left:334px">HOME</span>
  <span class="nav-link" style="left:415px">ABOUT US</span>
  <span class="nav-link" style="left:524px">OUR SERVICES</span>
  <span class="nav-link" style="left:664px">SOLUTIONS</span>
  <div class="btn" style="left:768px;top:15px;width:123px;height:48px">Contact Us</div>
  <div class="lang">
    <svg width="12" height="12" viewBox="0 0 12 12"><circle cx="6" cy="6" r="5.5" fill="var(--ink)"/><path d="M.5 6h11M6 .5c2 2 2 9 0 11M6 .5c-2 2-2 9 0 11" stroke="#fff" stroke-width=".8" fill="none"/></svg>
    ENG
  </div>
</nav>

<h1 class="abs hero-title">YOUR PARTNER<br>IN PAYROLLING<br>SOLUTIONS</h1>
<p class="abs hero-text">Flexible, transparent, &amp; compliant payroll services designed to make work easier for companies &amp; professionals.</p>
<div class="btn" style="left:112px;top:496px;width:130px;height:45px">Contact Us</div>

<!-- WHO WE ARE -->
<div class="abs about-ring" aria-hidden="true"></div>
<div class="abs about-photo" role="img" aria-label="Photo of two smiling colleagues working at an office desk"></div>

<h2 class="abs heading" style="left:640px;width:440px;top:885px;font-size:44px">WHO WE ARE</h2>
<div class="abs kicker" style="left:640px;width:440px;top:941px">ABOUT BRISK</div>
<p class="abs about-text" style="top:984px">Sed ut perspiciatis unde omnis iste natus error sit voluptatem accusantium doloremque laudantium, totam rem aperiam, eaque ipsa quae ab illo inventore veritatis et quasi architecto beatae vitae dicta sunt explicabo. Nemo enim ipsam voluptatem quia voluptas sit</p>
<p class="abs about-text" style="top:1159px">Neque porro quisquam est, qui dolorem ipsum quia dolor sit amet, consectetur, adipisci velit, sed quia non numquam eius modi tempora incidunt ut labore</p>
<div class="btn" style="left:767px;top:1270px;width:184px;height:49px">Explore More</div>

<!-- HOW IT WORKS -->
<h2 class="abs heading" style="top:1515px;font-size:46px">HOW IT WORKS</h2>
<div class="abs kicker" style="top:1572px">WHAT IS PAYROLLING?</div>
<p class="abs" style="left:0;width:1200px;top:1614px;text-align:center;font-size:17px;line-height:31px;color:#444">Payrolling is a smart employment model that allows companies to engage professionals<br>quickly, without taking on administrative burden or legal risk.</p>

<div class="abs step" style="left:121px">
  <div class="ico"><svg width="34" height="34" viewBox="0 0 34 34" fill="none" stroke="#fff" stroke-width="2"><rect x="8" y="5" width="12" height="25"/><rect x="20" y="13" width="8" height="17"/><path d="M11 10h6M11 15h6M11 20h6M4 30h27"/></svg></div>
  <h4>STEP 01</h4><p>Company selects the professional</p>
</div>
<div class="abs step" style="left:365px">
  <div class="ico"><svg width="34" height="34" viewBox="0 0 34 34" fill="none" stroke="#fff" stroke-width="2"><rect x="7" y="4" width="18" height="24" rx="2"/><path d="M11 10h10M11 15h10M11 20h6M20 27l4 3 7-8"/></svg></div>
  <h4>STEP 02</h4><p>BRISK The Answer hires them under contract</p>
</div>
<div class="abs step" style="left:608px">
  <div class="ico"><svg width="34" height="34" viewBox="0 0 34 34" fill="none" stroke="#fff" stroke-width="2"><circle cx="17" cy="10" r="5"/><circle cx="7" cy="15" r="3.5"/><circle cx="27" cy="15" r="3.5"/><path d="M8 29c0-6 4-10 9-10s9 4 9 10M1 28c0-4 2-7 6-7M33 28c0-4-2-7-6-7"/></svg></div>
  <h4>STEP 03</h4><p>Employee works for the company, salary paid by us</p>
</div>
<div class="abs step" style="left:852px">
  <div class="ico"><svg width="34" height="34" viewBox="0 0 34 34" fill="none" stroke="#fff" stroke-width="2"><circle cx="22" cy="11" r="5"/><path d="M22 3v3M22 16v3M14 11h3M27 11h3"/><circle cx="9" cy="13" r="4"/><path d="M2 30c0-6 3-9 7-9s6 2 8 5h8"/></svg></div>
  <h4>STEP 04</h4><p>We manage social charges, insurance, &amp; compliance</p>
</div>

<!-- WHAT IS PAYROLLING -->
<svg class="abs" style="left:0;top:2084px" width="1200" height="600" viewBox="0 0 1200 600">
  <defs><linearGradient id="payBand" x1="0" y1="0" x2="1" y2="1"><stop offset="0" stop-color="#e6007e"/><stop offset="1" stop-color="#c0006c"/></linearGradient></defs>
  <polygon points="0,0 1200,0 1200,500 0,585" fill="url(#payBand)"/>
</svg>
<div class="abs" role="img" aria-label="Faint city skyline overlay" style="left:0;top:2220px;width:1200px;height:380px;background:linear-gradient(180deg,rgba(255,255,255,0) 0%,rgba(80,0,50,.18) 100%);clip-path:polygon(0 0,100% 0,100% 95%,0 100%)"></div>

<h2 class="abs heading" style="top:2130px;font-size:44px;color:#fff">WHAT IS PAYROLLING?</h2>
<div class="abs kicker" style="top:2188px;color:#fff;font-size:21px">SMART WAY TO WORK.</div>

<div class="abs pay-card">
  <div class="dot" style="left:146px;top:42px;background:var(--ink)"><svg width="40" height="40" viewBox="0 0 34 34" fill="none" stroke="#fff" stroke-width="2"><circle cx="17" cy="10" r="5"/><circle cx="7" cy="15" r="3.5"/><circle cx="27" cy="15" r="3.5"/><path d="M8 29c0-6 4-10 9-10s9 4 9 10M1 28c0-4 2-7 6-7M33 28c0-4-2-7-6-7"/></svg></div>
  <div class="flow-label" style="left:89px;top:147px">COMPANY / CLIENT</div>
  <svg class="abs" style="left:280px;top:77px" width="42" height="16" viewBox="0 0 42 16"><path d="M0 8h40M33 2l7 6-7 6" fill="none" stroke="#555" stroke-width="2"/></svg>
  <div class="brand" style="left:358px;top:62px;font-size:40px;line-height:40px">BRISK<small style="display:block;font-size:9px;letter-spacing:6px;line-height:10px;font-weight:500">THE ANSWER</small></div>
  <svg class="abs" style="left:537px;top:77px" width="42" height="16" viewBox="0 0 42 16"><path d="M0 8h40M33 2l7 6-7 6" fill="none" stroke="#555" stroke-width="2"/></svg>
  <div class="dot" style="left:626px;top:42px;background:var(--pink)"><svg width="40" height="40" viewBox="0 0 34 34" fill="none" stroke="#fff" stroke-width="2"><circle cx="15" cy="10" r="6"/><path d="M4 30c0-7 5-11 11-11s11 4 11 11"/><circle cx="27" cy="9" r="3"/></svg></div>
  <div class="flow-label" style="left:569px;top:147px">EMPLOYEE / PROFESSIONAL</div>

  <div class="abs" style="left:54px;top:227px;font-size:21px;font-weight:700">IN SIMPLE WORDS:</div>
  <svg class="abs" style="left:56px;top:274px" width="16" height="12"><path d="M1 6l4 4 9-9" fill="none" stroke="#555" stroke-width="2.5"/></svg>
  <div class="list-item" style="left:86px;top:265px;width:300px">The company chooses the professional.</div>
  <svg class="abs" style="left:56px;top:332px" width="16" height="12"><path d="M1 6l4 4 9-9" fill="none" stroke="#555" stroke-width="2.5"/></svg>
  <div class="list-item" style="left:86px;top:323px;width:310px">BRISK The Answer becomes the official employer.</div>
  <svg class="abs" style="left:56px;top:420px" width="16" height="12"><path d="M1 6l4 4 9-9" fill="none" stroke="#555" stroke-width="2.5"/></svg>
  <div class="list-item" style="left:86px;top:411px;width:310px">The professional works for the company, and we take care of contracts, payroll, and social contributions.</div>

  <div class="abs" style="left:431px;top:224px;height:275px;border-left:2px dashed var(--pink);opacity:.7"></div>

  <svg class="abs" style="left:479px;top:232px" width="16" height="16"><rect x="1" y="1" width="14" height="14" rx="2" fill="var(--pink)"/><path d="M4 8l3 3 5-6" fill="none" stroke="#fff" stroke-width="2"/></svg>
  <div class="list-item" style="left:512px;top:225px;width:320px"><b>For companies:</b> No administrative or legal risk.</div>
  <svg class="abs" style="left:479px;top:318px" width="16" height="16"><rect x="1" y="1" width="14" height="14" rx="2" fill="var(--pink)"/><path d="M4 8l3 3 5-6" fill="none" stroke="#fff" stroke-width="2"/></svg>
  <div class="list-item" style="left:512px;top:311px;width:320px"><b>For professionals:</b> Employment security and full social benefits.</div>
  <svg class="abs" style="left:479px;top:405px" width="16" height="16"><rect x="1" y="1" width="14" height="14" rx="2" fill="var(--pink)"/><path d="M4 8l3 3 5-6" fill="none" stroke="#fff" stroke-width="2"/></svg>
  <div class="list-item" style="left:512px;top:398px;width:320px"><b>For everyone:</b> Simplicity, compliance, transparency.</div>
</div>

<!-- SERVICES -->
<h2 class="abs heading" style="top:2908px;font-size:46px">SERVICES WE OFFER</h2>
<div class="abs kicker" style="top:2965px">WHAT WE DO</div>

<div class="abs svc" style="left:103px">
  <div class="pic" role="img" aria-label="Photo of a hand pointing at glowing financial charts" style="background:linear-gradient(160deg,#3b4a66 0%,#1d2435 60%,#6a5a48 100%)"></div>
  <h4>FOR COMPANIES</h4>
  <p>Flexible workforce solutions, simplified HR processes, compliance &amp; cost transparency</p>
</div>
<div class="abs svc" style="left:446px">
  <div class="pic" role="img" aria-label="Photo of a presenter leading a meeting in a bright conference room" style="background:linear-gradient(160deg,#cfd6da 0%,#8f9aa0 55%,#3c4145 100%)"></div>
  <h4>FOR PROFESSIONALS</h4>
  <p>Employment security, social benefits, pension contributions, regular pay</p>
</div>
<div class="abs svc" style="left:789px">
  <div class="pic" role="img" aria-label="Photo of a consultant in a suit reviewing printed reports" style="background:linear-gradient(160deg,#2a3243 0%,#596377 55%,#c9ced6 100%)"></div>
  <h4>FOR FREELANCERS AND CONSULTANTS</h4>
  <p>Freedom to work with clients while enjoying employee protection</p>
</div>

<!-- CONTACT -->
<h2 class="abs heading" style="top:3595px;font-size:46px">LET’S TALK PAYROLL</h2>
<div class="abs kicker" style="top:3655px">GET IN TOUCH</div>

<div class="field" style="left:227px;top:3726px;width:359px;height:49px">
  <svg width="12" height="12" viewBox="0 0 12 12" fill="#555"><circle cx="6" cy="3.5" r="3"/><path d="M0 12c0-4 3-5.5 6-5.5s6 1.5 6 5.5z"/></svg>FULL NAME</div>
<div class="field" style="left:227px;top:3800px;width:359px;height:49px">
  <svg width="13" height="10" viewBox="0 0 13 10"><rect width="13" height="10" rx="1" fill="#555"/><path d="M0 1l6.5 5L13 1" stroke="#efefef" fill="none"/></svg>EMAIL ADDRESS</div>
<div class="field" style="left:227px;top:3873px;width:359px;height:49px">
  <svg width="12" height="12" viewBox="0 0 12 12" fill="#555"><path d="M2.5 0l2 3-1.3 1.3a7 7 0 0 0 4.5 4.5L9 7.5l3 2-1 2.5C5 12 0 7 0 1z"/></svg>CONTACT NUMBER</div>
<div class="btn" style="left:227px;top:3946px;width:359px;height:51px;font-weight:500;font-size:13px">SEND MESSAGE</div>
<div class="field" style="left:614px;top:3726px;width:357px;height:267px;border-radius:18px;align-items:flex-start;padding-top:20px">
  <svg width="13" height="11" viewBox="0 0 13 11" fill="#555"><path d="M6.5 0C10 0 13 2 13 4.5S10 9 6.5 9L3 11V8.3C1 7.5 0 6 0 4.5 0 2 3 0 6.5 0z"/></svg>COMMENTS</div>

<!-- FOOTER -->
<svg class="abs" style="left:0;top:3980px" width="1200" height="671" viewBox="0 0 1200 671">
  <polygon points="0,8 1200,230 1200,671 0,671" fill="var(--pink)"/>
  <polygon points="0,110 1200,230 1200,671 0,671" fill="var(--ink)"/>
  <polygon points="307,207 348,230 348,275 307,298 266,275 266,230" fill="#fff"/>
  <path d="M307 270v-30M296 251l11-11 11 11" stroke="var(--pink)" stroke-width="5" fill="none"/>
</svg>

<div class="brand" style="left:110px;top:4330px;font-size:78px;line-height:78px;color:#fff;letter-spacing:3px">BRISK</div>
<div class="abs" style="left:112px;top:4406px;font-family:'Outfit',sans-serif;font-size:18px;letter-spacing:17px;color:#fff">THE ANSWER</div>

<div class="foot-h" style="left:473px;top:4337px">QUICK LINKS</div>
<div class="foot-i" style="left:473px;top:4381px"><svg width="14" height="14"><circle cx="7" cy="7" r="6.5" fill="#fff"/><path d="M5 4l3 3-3 3" stroke="var(--ink)" stroke-width="2" fill="none"/></svg>Home</div>
<div class="foot-i" style="left:473px;top:4414px"><svg width="14" height="14"><circle cx="7" cy="7" r="6.5" fill="#fff"/><path d="M5 4l3 3-3 3" stroke="var(--ink)" stroke-width="2" fill="none"/></svg>Who we are</div>
<div class="foot-i" style="left:473px;top:4448px"><svg width="14" height="14"><circle cx="7" cy="7" r="6.5" fill="#fff"/><path d="M5 4l3 3-3 3" stroke="var(--ink)" stroke-width="2" fill="none"/></svg>Services</div>
<div class="foot-i" style="left:473px;top:4482px"><svg width="14" height="14"><circle cx="7" cy="7" r="6.5" fill="#fff"/><path d="M5 4l3 3-3 3" stroke="var(--ink)" stroke-width="2" fill="none"/></svg>Our solutions</div>
<div class="foot-i" style="left:473px;top:4515px"><svg width="14" height="14"><circle cx="7" cy="7" r="6.5" fill="#fff"/><path d="M5 4l3 3-3 3" stroke="var(--ink)" stroke-width="2" fill="none"/></svg>Contact Us</div>

<div class="foot-h" style="left:689px;top:4337px">CONTACT INFO</div>
<div class="foot-i" style="left:689px;top:4381px;align-items:flex-start"><svg width="12" height="16" viewBox="0 0 12 16"><path d="M6 0a6 6 0 0 1 6 6c0 4-6 10-6 10S0 10 0 6a6 6 0 0 1 6-6z" fill="#fff"/><circle cx="6" cy="6" r="2.2" fill="var(--ink)"/></svg><span style="line-height:33px;margin-top:-8px">BRISK The Answer<br>Rue des Tilleuls 22<br>1205 Geneva, Switzerland</span></div>
<div class="foot-i" style="left:689px;top:4482px"><svg width="14" height="11" viewBox="0 0 13 10"><rect width="13" height="10" rx="1" fill="#fff"/><path d="M0 1l6.5 5L13 1" stroke="var(--ink)" fill="none"/></svg>info@brisktheanswer.com</div>
<div class="foot-i" style="left:689px;top:4515px"><svg width="13" height="13" viewBox="0 0 12 12" fill="#fff"><path d="M2.5 0l2 3-1.3 1.3a7 7 0 0 0 4.5 4.5L9 7.5l3 2-1 2.5C5 12 0 7 0 1z"/></svg>+41 22 555 01 23</div>

<div class="social" style="left:957px"></div>
<div class="social" style="left:1004px"></div>
<div class="social" style="left:1049px"></div>

<div class="abs" style="left:112px;top:4585px;width:976px;border-top:1px dotted #777"></div>
<div class="abs" style="left:0;width:1200px;top:4612px;text-align:center;font-size:13px;color:#fff">(C) Copyright 2025 | All Rights Reserved</div>

</body>
</html>
```